Bramble firearms training and consulting

Business card for a new firearms training company. I train persons on firearms safety, personal protection, shooting tactics and CHL.Im a Prior State trooper. I also served 4 years in IRaq as a Protection contractor with the Dept of State. Real world training for Real world situations. I would like the company name to be, BRAMBLE FIREARMS TRAINING AND CONSULTING. Im native american also. Ive provided pics. Put the name Bramble above the arrowhead but rotate the arrowhead to the right with it pointing right. Then place bramble inside the arrowhead. lets see both.
Industry/Entity Type
Business
Contact Information for Business Card
Christian Chatellier817-240-0488shadowtraining33@gmail.com

```html
<!DOCTYPE html>
<html lang="en">
<head>
<meta charset="utf-8">
<title>Bramble Firearms Training and Consulting – Business Card</title>
<link rel="stylesheet" href="https://fonts.googleapis.com/css2?family=Marcellus&family=Arimo:wght@400&display=swap">
<style>
  :root {
    --backdrop: #1d1d1d;
    --card: #fbfbfa;
    --maroon: #7c1709;
    --maroon-light: #982417;
    --ink: #141414;
  }
  * { margin: 0; padding: 0; box-sizing: border-box; }
  html, body {
    width: 1200px;
    height: 1198px;
    overflow: hidden;
    background: var(--backdrop);
  }
  .card {
    position: absolute;
    left: 233px;
    top: 22px;
    width: 701px;
    height: 1150px;
    background: var(--card);
  }
  .band {
    position: absolute;
    left: 181px;
    width: 338px;
    background: var(--maroon);
  }
  .band--top { top: 0; height: 44px; }
  .band--top-rule { top: 50px; height: 4px; }
  .band--bottom-rule { bottom: 50px; height: 4px; }
  .band--bottom { bottom: 0; height: 44px; }

  .holder {
    position: absolute;
    top: 112px;
    width: 100%;
    text-align: center;
    font-family: "Marcellus", serif;
    color: var(--ink);
  }
  .holder__name { font-size: 50px; font-weight: 400; line-height: 1; }
  .holder__role { font-size: 22px; margin-top: 8px; }

  .brand {
    position: absolute;
    top: 472px;
    width: 100%;
    text-align: center;
    font-family: "Marcellus", serif;
    font-size: 96px;
    letter-spacing: 6px;
    line-height: 1;
    color: var(--maroon);
  }
  .tagline {
    position: absolute;
    top: 628px;
    width: 100%;
    text-align: center;
    font-family: "Arimo", sans-serif;
    font-size: 29px;
    color: var(--maroon-light);
  }

  .contact {
    position: absolute;
    top: 918px;
    left: 0;
    width: 100%;
    list-style: none;
    font-family: "Marcellus", serif;
    font-size: 29px;
    color: var(--ink);
    display: flex;
    flex-direction: column;
    align-items: center;
    gap: 10px;
  }
  .contact__item { display: flex; align-items: center; gap: 14px; height: 36px; }
  .contact__icon { width: 30px; height: 30px; flex: none; }
</style>
</head>
<body>
  <main class="card">
    <div class="band band--top"></div>
    <div class="band band--top-rule"></div>

    <header class="holder">
      <h1 class="holder__name">Dorian Pellwick</h1>
      <p class="holder__role">Trainer and Consultant</p>
    </header>

    <div class="brand">BRAMBLE</div>
    <p class="tagline">FIREARMS TRAINING AND CONSULTING</p>

    <ul class="contact">
      <li class="contact__item">
        <svg class="contact__icon" viewBox="0 0 32 32" aria-hidden="true">
          <circle cx="16" cy="16" r="14" fill="none" stroke="#141414" stroke-width="2.5"/>
          <path d="M11 9c1-1 2-1 3 0l1.5 2.5c.5 1 0 1.8-.8 2.4-.6.5-.6 1 0 2l1.5 1.8c.8.8 1.3.9 2 .3.8-.7 1.6-1 2.4-.4L23 19c1 1 .9 2-.2 3-2 2-5 1-8.3-2.3S9 13 11 9z" fill="#141414"/>
        </svg>
        <span>555-317-9062</span>
      </li>
      <li class="contact__item">
        <svg class="contact__icon" viewBox="0 0 32 32" aria-hidden="true">
          <circle cx="16" cy="16" r="15" fill="#141414"/>
          <rect x="8" y="13" width="16" height="6" rx="1" fill="#fbfbfa"/>
        </svg>
        <span>bramblecourse58@mailvento.com</span>
      </li>
      <li class="contact__item">
        <svg class="contact__icon" viewBox="0 0 32 32" aria-hidden="true">
          <circle cx="16" cy="16" r="15" fill="#141414"/>
          <path d="M16 8l-8 7h2.5v8h4.5v-5h2v5h4.5v-8H24z" fill="#fbfbfa"/>
        </svg>
        <span>48 Larkspur Lane, Fenwick, NY 12847</span>
      </li>
    </ul>

    <div class="band band--bottom-rule"></div>
    <div class="band band--bottom"></div>
  </main>
</body>
</html>
```